Business Cards for a law firm

Business cards for our law firm. Use our silhoette logo and OAK PARTNERS - check our website (www.oakpartners.example)

Contact Information for Business Card

our silhouette logo, OAK PARTNERS, 800-555-0147, Dorian Pemberton, dorian@oakpartners.example

Requirements
Must have
• our silhouette logo, OAK PARTNERS, 800-555-0147, Dorian Pemberton, dorian@oakpartners.example

```html
<!DOCTYPE html>
<html lang="en">
<head>
<meta charset="utf-8">
<title>Oak Partners – Business Card</title>
<link href="https://fonts.googleapis.com/css2?family=Mulish:wght@400;700;800&display=swap" rel="stylesheet">
<style>
  :root {
    --backdrop: #e5e5e5;
    --card: #ffffff;
    --ink: #000000;
  }
  * { margin: 0; padding: 0; box-sizing: border-box; }
  html, body { width: 1200px; height: 1200px; overflow: hidden; }
  body { background: var(--backdrop); position: relative; font-family: "Mulish", sans-serif; color: var(--ink); }

  .card { position: absolute; left: 215px; width: 770px; height: 440px; background: var(--card); }
  .card--front { top: 141px; }
  .card--back { top: 619px; }

  .contact-row { position: absolute; left: 32px; display: flex; align-items: center; white-space: nowrap; }
  .contact-row .icon { width: 20px; height: 20px; display: flex; align-items: center; justify-content: center; }
  .contact-row .icon svg { width: 100%; height: 100%; }
  .contact-row .divider { width: 1.2px; background: var(--ink); margin: 0 6px 0 6px; }

  .holder { top: 236px; }
  .holder .divider { height: 28px; }
  .holder .label { font-weight: 700; font-size: 29px; letter-spacing: 0.2px; }

  .detail .divider { height: 20px; }
  .detail .label { font-weight: 400; font-size: 17px; letter-spacing: 0.2px; }
  .detail--phone { top: 297px; }
  .detail--mail { top: 325px; }
  .detail--web { top: 353px; }
  .detail--place { top: 384px; }

  .edge-bar { position: absolute; right: 0; top: 0; width: 9px; height: 100%; background: var(--ink); }

  .brand-mark { position: absolute; left: 36px; top: 286px; width: 64px; height: 64px; background: var(--ink); }
  .brand-name { position: absolute; left: 126px; top: 296px; font-weight: 800; font-size: 44px; letter-spacing: 2px; line-height: 1; white-space: nowrap; }
</style>
</head>
<body>
  <section class="card card--front">
    <div class="contact-row holder">
      <span class="icon">
        <svg viewBox="0 0 20 20"><circle cx="10" cy="6" r="4.2" fill="currentColor"/><path d="M1 19 C1 13 5 11 10 11 C15 11 19 13 19 19 Z" fill="currentColor"/></svg>
      </span>
      <span class="divider"></span>
      <span class="label">Dorian Pemberton</span>
    </div>

    <div class="contact-row detail detail--phone">
      <span class="icon">
        <svg viewBox="0 0 24 24"><path d="M6.6 10.8c1.4 2.8 3.8 5.1 6.6 6.6l2.2-2.2c.3-.3.7-.4 1-.2 1.1.4 2.3.6 3.6.6.6 0 1 .4 1 1V20c0 .6-.4 1-1 1C10.6 21 3 13.4 3 4c0-.6.4-1 1-1h3.5c.6 0 1 .4 1 1 0 1.3.2 2.5.6 3.6.1.3 0 .7-.2 1L6.6 10.8z" fill="currentColor"/></svg>
      </span>
      <span class="divider"></span>
      <span class="label">800-555-0147</span>
    </div>

    <div class="contact-row detail detail--mail">
      <span class="icon">
        <svg viewBox="0 0 24 24"><rect x="2" y="5" width="20" height="14" rx="2" fill="none" stroke="currentColor" stroke-width="2"/><path d="M3 6l9 7 9-7" fill="none" stroke="currentColor" stroke-width="2"/></svg>
      </span>
      <span class="divider"></span>
      <span class="label">dorian@oakpartners.example</span>
    </div>

    <div class="contact-row detail detail--web">
      <span class="icon">
        <svg viewBox="0 0 24 24" fill="none" stroke="currentColor" stroke-width="1.5"><circle cx="12" cy="12" r="10"/><ellipse cx="12" cy="12" rx="4.5" ry="10"/><path d="M2 12h20M4 6.5h16M4 17.5h16M12 2v20"/></svg>
      </span>
      <span class="divider"></span>
      <span class="label">Www.yourweb.com</span>
    </div>

    <div class="contact-row detail detail--place">
      <span class="icon">
        <svg viewBox="0 0 24 24"><path d="M12 2a7 7 0 0 0-7 7c0 5 7 13 7 13s7-8 7-13a7 7 0 0 0-7-7zm0 9.5A2.5 2.5 0 1 1 12 6.5a2.5 2.5 0 0 1 0 5z" fill="currentColor"/></svg>
      </span>
      <span class="divider"></span>
      <span class="label">Your street, sity, state, sountry</span>
    </div>
  </section>

  <section class="card card--back">
    <div class="brand-mark"></div>
    <div class="brand-name">OAK PARTNERS</div>
    <div class="edge-bar"></div>
  </section>
</body>
</html>
```